Im open to ideas.. I was thinking on my business cards aswell as my logo. a place for my name. email. phone number and abn..

ive attched a file with my business logo. which i dont love the colours.. i was think a dark background with charcoal letters so something along those colour schumes but im open to ideas..

BRM Constructions

```html
<!DOCTYPE html>
<html lang="en">
<head>
<meta charset="utf-8">
<title>BRM Constructions – Business Card</title>
<link rel="stylesheet" href="https://fonts.googleapis.com/css2?family=Montserrat:wght@400;500;700&display=swap">
<style>
  :root {
    --page-bg: #e9e7e3;
    --card-bg: #ffffff;
    --ink: #2b2b2b;
    --ink-soft: #3a3a3a;
    --accent: #e5203a;
    --rule: #555555;
  }
  * { box-sizing: border-box; margin: 0; padding: 0; }
  html, body {
    width: 1200px;
    height: 1022px;
    overflow: hidden;
    background: var(--page-bg);
    font-family: "Montserrat", Arial, sans-serif;
  }
  .card {
    position: absolute;
    left: 100px;
    top: 225px;
    width: 1000px;
    height: 572px;
    background: var(--card-bg);
    border-radius: 22px;
    box-shadow: 0 10px 30px rgba(0,0,0,0.12);
    display: flex;
    align-items: center;
  }
  .brand {
    width: 490px;
    padding: 0 30px;
    display: flex;
    align-items: center;
    justify-content: center;
    gap: 16px;
  }
  .brand-square {
    width: 24px;
    height: 24px;
    flex: none;
    background: var(--accent);
  }
  .brand-name {
    font-size: 35px;
    font-weight: 700;
    color: var(--ink);
    letter-spacing: 0.5px;
    white-space: nowrap;
  }
  .divider {
    width: 2px;
    height: 200px;
    flex: none;
    background: var(--rule);
  }
  .details {
    padding-left: 52px;
    color: var(--ink-soft);
  }
  .person-name {
    font-size: 36px;
    font-weight: 700;
    color: var(--accent);
    letter-spacing: 1px;
    text-transform: uppercase;
  }
  .person-role {
    font-size: 22px;
    font-weight: 400;
    margin-top: 4px;
  }
  .abn {
    font-size: 23px;
    margin-top: 14px;
  }
  .abn-label {
    color: var(--accent);
    font-weight: 700;
  }
  .contact-list {
    list-style: none;
    margin-top: 14px;
  }
  .contact-item {
    display: flex;
    align-items: center;
    gap: 16px;
    font-size: 23px;
    line-height: 38px;
    white-space: nowrap;
  }
  .contact-icon {
    width: 18px;
    height: 18px;
    flex: none;
  }
  .web-domain { color: var(--accent); }
</style>
</head>
<body>
  <div class="card">
    <div class="brand">
      <span class="brand-square"></span>
      <span class="brand-name">BRM Constructions</span>
    </div>
    <div class="divider"></div>
    <div class="details">
      <p class="person-name">Daniel Hartley</p>
      <p class="person-role">Director</p>
      <p class="abn"><span class="abn-label">ABN</span>: 51 824 603 117</p>
      <ul class="contact-list">
        <li class="contact-item">
          <svg class="contact-icon" viewBox="0 0 24 24" aria-hidden="true">
            <path d="M6.6 2.5l3 3.5-2 2.2a14 14 0 0 0 8.2 8.2l2.2-2 3.5 3-2.3 3.1C11 20.2 3.8 13 3.5 4.8z" fill="none" stroke="var(--accent)" stroke-width="2.2" stroke-linejoin="round"/>
          </svg>
          +44 1632 960 518
        </li>
        <li class="contact-item">
          <svg class="contact-icon" viewBox="0 0 24 24" aria-hidden="true">
            <rect x="2.5" y="5" width="19" height="14" rx="1.5" fill="none" stroke="var(--accent)" stroke-width="2.2"/>
            <path d="M3 6l9 7 9-7" fill="none" stroke="var(--accent)" stroke-width="2.2"/>
          </svg>
          info@brmconstructions.com
        </li>
        <li class="contact-item">
          <svg class="contact-icon" viewBox="0 0 24 24" aria-hidden="true">
            <circle cx="12" cy="12" r="9.5" fill="none" stroke="var(--accent)" stroke-width="2.2"/>
            <ellipse cx="12" cy="12" rx="4" ry="9.5" fill="none" stroke="var(--accent)" stroke-width="1.8"/>
            <path d="M2.5 12h19M4 7h16M4 17h16" stroke="var(--accent)" stroke-width="1.8"/>
          </svg>
          <span>www.<span class="web-domain">brmconstructions</span>.com</span>
        </li>
      </ul>
    </div>
  </div>
</body>
</html>
```